Bramblewood Joinery Website

My client Bramblewood Joinery is looking for a redesign for a Word Press Website. Their current site is at www.bramblewoodjoinery.example They are a custom cabinet company, but also create bathroom, living room, bar and entertainment and bedroom cabinets too. They would like a design that emulates the master craftsman work they do yet a contemporary style.

Their current site was designed using Flash elements.

Target Market(s)

Home owners and builders of high end homes

Industry/Entity Type

Entertainment

Font styles to use
Serif
Decorative

Requirements
Must have
• Must show their work and logo using a contemporary style.
Nice to have
• Sliders that showcase their projects.

```html
<!DOCTYPE html>
<html lang="en">
<head>
<meta charset="utf-8">
<title>Bramblewood Joinery</title>
<link href="https://fonts.googleapis.com/css2?family=Noto+Serif:ital,wght@0,400;0,700;1,700&family=Mulish:wght@400;600;700&family=Roboto+Condensed:wght@400;700&family=Roboto:wght@700;900&display=swap" rel="stylesheet">
<style>
:root{
  --green:#2db82d;
  --green-light:#8cc63f;
  --ink:#2e2e2e;
  --text:#444;
  --grey-bar:#3b3839;
  --footer:#1c1c1c;
  --footer-text:#c9c9c9;
  --white:#fff;
}
*{margin:0;padding:0;box-sizing:border-box}
html,body{width:960px;height:1200px;overflow:hidden;background:var(--white)}
body{position:relative;font-family:"Mulish",sans-serif;color:var(--text)}
.abs{position:absolute}
.topline{left:0;top:0;width:960px;height:2px;background:#333}
.brand{left:86px;top:22px;display:flex;align-items:center;gap:10px}
.brand-dot{width:26px;height:26px;border-radius:50%;background:var(--green)}
.brand-name{font-family:"Noto Serif",serif;font-weight:700;font-size:20px;color:var(--ink)}
.search{left:482px;top:30px;width:154px;height:26px;border:1px solid #ccc;border-radius:13px;background:#f3f3f3}
.search svg{position:absolute;right:8px;top:6px}
.badge{top:28px;display:flex;align-items:center;gap:8px;font-family:"Roboto Condensed",sans-serif;color:#555;line-height:1.1}
.badge small{display:block;font-size:8px;color:#333}
.badge span{font-size:11px;color:#777}
.nav{left:0;top:85px;width:960px;height:40px;background:var(--green)}
.nav ul{list-style:none;display:flex;gap:18px;position:absolute;left:184px;top:13px;font-family:"Noto Serif",serif;font-size:11px;color:var(--white)}
.hero{left:0;top:125px;width:960px;height:397px;background:linear-gradient(180deg,#d8cfc2 0%,#b9a896 45%,#5a4032 80%,#3c2a20 100%)}
.hero h1{position:absolute;width:960px;top:326px;text-align:center;font-family:"Noto Serif",serif;font-style:italic;font-weight:700;font-size:39px;color:var(--white)}
.arrow{top:533px;width:16px;height:69px;background:var(--green)}
.arrow svg{position:absolute;left:4px;top:30px}
.thumb{top:533px;width:142px;height:69px;background:linear-gradient(180deg,#cfc2b0,#8a7563 60%,#4e3a2e)}
.thumb.active{border:2px solid var(--green);background:linear-gradient(180deg,#4a4a4a,#2a2a2a)}
.about h2{position:absolute;left:90px;top:643px;font-family:"Noto Serif",serif;font-weight:400;font-size:21px;color:var(--ink)}
.about p{position:absolute;left:90px;top:680px;width:490px;font-size:11.2px;line-height:20px;color:var(--text)}
.video-tag{left:600px;top:637px;width:142px;height:21px;background:var(--green);color:var(--white);font-family:"Noto Serif",serif;font-weight:700;font-size:15px;padding-left:10px;line-height:21px}
.video{left:612px;top:658px;width:257px;height:144px;background:var(--white);box-shadow:0 2px 6px rgba(0,0,0,.35);padding:6px}
.video-screen{width:100%;height:100%;background:linear-gradient(135deg,#3a3a3a,#8f8478 55%,#d9cfc0)}
.video-bar{position:absolute;left:6px;bottom:6px;width:245px;height:16px;background:#222}
.play{left:717px;top:705px;width:52px;height:34px;background:rgba(0,0,0,.75)}
.stats{left:0;top:838px;width:960px;height:88px;background:var(--green)}
.stat{top:857px;display:flex;gap:16px;align-items:center;color:var(--white)}
.stat b{display:block;font-family:"Roboto",sans-serif;font-weight:900;font-size:24px;line-height:1}
.stat span{display:block;font-family:"Roboto Condensed",sans-serif;font-size:14px;margin-top:6px}
.social-bar{left:0;top:926px;width:960px;height:55px;background:var(--grey-bar)}
.soc{top:937px;width:33px;height:33px;border-radius:50%;background:var(--white)}
.email{left:441px;top:939px;width:275px;height:28px;background:var(--white);font-family:"Roboto Condensed",sans-serif;font-size:11px;color:#666;padding:7px 11px}
.subscribe{left:725px;top:939px;width:137px;height:28px;background:var(--green-light);color:var(--white);font-family:"Roboto Condensed",sans-serif;font-weight:700;font-size:16px;text-align:center;line-height:28px}
.footer{left:0;top:981px;width:960px;height:219px;background:var(--footer)}
.fcol{top:1016px;color:var(--footer-text);font-size:10.5px}
.fcol h3{font-size:13px;font-weight:700;color:var(--white);margin-bottom:14px}
.fcol ul{list-style:none;line-height:17.6px}
.fcol li:before{content:"• "}
.ci{display:flex;gap:8px;line-height:17.6px;margin-bottom:10px}
.ci svg{flex:none;margin-top:3px}
.fdots{display:flex;gap:7px;margin:6px 0 16px}
.fdots i{width:21px;height:21px;border-radius:50%;background:#4a4a4a;display:block}
.fbrand{font-size:14px;font-weight:700;color:var(--white);display:flex;align-items:center;gap:8px;margin-bottom:12px}
.fbrand i{width:14px;height:14px;border-radius:50%;background:#888;display:block}
.fseal{left:738px;top:1040px;width:102px;height:102px;border-radius:50%;border:3px solid #555;display:flex;align-items:center;justify-content:center;text-align:center;font-family:"Noto Serif",serif;font-weight:700;font-size:12px;color:#666;line-height:1.3}
</style>
</head>
<body>
<div class="abs topline"></div>

<header>
  <div class="abs brand"><div class="brand-dot"></div><div class="brand-name">Bramblewood Joinery</div></div>
  <div class="abs search"><svg width="12" height="12" viewBox="0 0 12 12"><circle cx="5" cy="5" r="3.8" fill="none" stroke="#888" stroke-width="1.6"/><line x1="8" y1="8" x2="11" y2="11" stroke="#888" stroke-width="1.8"/></svg></div>
  <div class="abs badge" style="left:656px">
    <svg width="30" height="30" viewBox="0 0 30 30"><circle cx="15" cy="14" r="10" fill="none" stroke="#666" stroke-width="3"/><rect x="3" y="12" width="5" height="8" rx="2" fill="#666"/><rect x="22" y="12" width="5" height="8" rx="2" fill="#666"/><path d="M24 20 Q22 27 15 27" fill="none" stroke="#666" stroke-width="1.5"/></svg>
    <div><small>CUSTOMER</small><span>SUPPORT</span></div>
  </div>
  <div class="abs badge" style="left:762px">
    <svg width="30" height="30" viewBox="0 0 30 30"><rect x="2" y="8" width="18" height="18" fill="none" stroke="#555" stroke-width="2"/><path d="M6 16 L12 23 L28 2" fill="none" stroke="var(--green-light)" stroke-width="5"/></svg>
    <div><small>100% CUSTOMER</small><span>SATISFACTION</span></div>
  </div>
  <nav class="abs nav">
    <ul><li>HOME</li><li>WHO WE ARE</li><li>GETTING STARTED</li><li>CUSTOMER EXPERIENCE</li><li>PROFESSIONAL</li><li>PORTFOLIO</li><li>CABINET HARDWARE</li></ul>
  </nav>
</header>

<section class="abs hero" role="img" aria-label="Photo of a bright kitchen with white cabinets, a dark wood island and dark hardwood floor">
  <h1>Best Cabinet and Fixtures</h1>
</section>

<div class="abs arrow" style="left:88px"><svg width="8" height="10" viewBox="0 0 8 10"><path d="M6 1 L2 5 L6 9" fill="none" stroke="#fff" stroke-width="2"/></svg></div>
<div class="abs thumb" style="left:110px" role="img" aria-label="Kitchen project with wall oven"></div>
<div class="abs thumb active" style="left:259px" role="img" aria-label="Dark kitchen project"></div>
<div class="abs thumb" style="left:407px" role="img" aria-label="Kitchen project with island"></div>
<div class="abs thumb" style="left:556px" role="img" aria-label="Kitchen project with pendant lights"></div>
<div class="abs thumb" style="left:706px" role="img" aria-label="Kitchen project with glass cabinets"></div>
<div class="abs arrow" style="left:855px"><svg width="8" height="10" viewBox="0 0 8 10"><path d="M2 1 L6 5 L2 9" fill="none" stroke="#fff" stroke-width="2"/></svg></div>

<section class="about">
  <h2>WHO WE ARE</h2>
  <p>Established in 1966, Bramblewood Joinery has long stood as one of the Midwest's most renowned makers of custom cabinets and fixtures. Our handcrafted, award-winning creations have been chosen by hundreds of noteworthy homebuilders. And while we custom build cabinets, we built our business around the belief that our customers absolutely, unequivocally come first. From day one, our mission has been to help turn the houses that people live in to the homes they've always dreamed of.</p>
</section>

<div class="abs video-tag">Featured Video</div>
<div class="abs video">
  <div class="video-screen" role="img" aria-label="Video still of a kitchen with a stainless wall oven"></div>
  <div class="video-bar"></div>
</div>
<div class="abs play"><svg width="52" height="34" viewBox="0 0 52 34"><path d="M21 9 L33 17 L21 25 Z" fill="#fff"/></svg></div>

<section class="abs stats"></section>
<div class="abs stat" style="left:98px">
  <svg width="32" height="44" viewBox="0 0 32 44"><rect x="2" y="6" width="24" height="34" rx="2" fill="none" stroke="#fff" stroke-width="3"/><rect x="9" y="2" width="10" height="7" fill="#fff"/><path d="M8 28 L14 35 L30 16" fill="none" stroke="#fff" stroke-width="4"/></svg>
  <div><b>520</b><span>COMPLETED PROJECTS</span></div>
</div>
<div class="abs stat" style="left:386px">
  <svg width="48" height="42" viewBox="0 0 48 42"><rect x="1" y="1" width="46" height="40" rx="4" fill="#fff"/><rect x="8" y="12" width="32" height="24" fill="var(--green)"/><text x="24" y="31" text-anchor="middle" font-family="Roboto,sans-serif" font-weight="900" font-size="16" fill="#fff">14</text></svg>
  <div><b>14</b><span>YEARS OF EXPERIENCE</span></div>
</div>
<div class="abs stat" style="left:698px">
  <svg width="36" height="44" viewBox="0 0 36 44"><g fill="#fff"><circle cx="8" cy="6" r="4"/><circle cx="18" cy="8" r="4.5"/><circle cx="28" cy="6" r="4"/><rect x="3" y="12" width="10" height="18" rx="2"/><rect x="23" y="12" width="10" height="18" rx="2"/><rect x="12" y="14" width="12" height="28" rx="2"/></g></svg>
  <div><b>180</b><span>HAPPY CLIENTS</span></div>
</div>

<section class="abs social-bar"></section>
<div class="abs soc" style="left:100px"></div>
<div class="abs soc" style="left:149px"></div>
<div class="abs soc" style="left:198px"></div>
<div class="abs soc" style="left:247px"></div>
<div class="abs email">Enter your email id and get updates!</div>
<div class="abs subscribe">SUBSCRIBE</div>

<footer class="abs footer"></footer>
<div class="abs fcol" style="left:98px">
  <h3>Site Map</h3>
  <ul><li>Home</li><li>Who We Are</li><li>Getting Started</li><li>Customer Experience</li><li>Professional</li><li>Portfolio</li></ul>
</div>
<div class="abs fcol" style="left:258px">
  <h3>Contact us</h3>
  <div class="ci"><svg width="10" height="13" viewBox="0 0 10 13"><path d="M5 12 C1 7 1 5 1 4.5 A4 4 0 0 1 9 4.5 C9 5 9 7 5 12Z" fill="#888"/><circle cx="5" cy="4.5" r="1.5" fill="#1c1c1c"/></svg><div>Bramblewood Joinery Owen Harcourt<br>4820 Elm Crest Road Fairview,<br>MO 64000</div></div>
  <div class="ci"><svg width="12" height="12" viewBox="0 0 12 12"><path d="M2 1 L4.5 1 L5.5 4 L4 5 Q5 8 7 8.5 L8 7 L11 8 L11 10.5 Q7 12 3.5 8 Q0 4 2 1Z" fill="#888"/></svg><div>555.014.2280</div></div>
  <div class="ci"><svg width="13" height="9" viewBox="0 0 13 9"><rect x="0.5" y="0.5" width="12" height="8" fill="none" stroke="#888"/><path d="M0.5 0.5 L6.5 5 L12.5 0.5" fill="none" stroke="#888"/></svg><div>info@bramblewood.example</div></div>
</div>
<div class="abs fcol" style="left:521px">
  <h3>Follow Us</h3>
  <div class="fdots"><i></i><i></i><i></i><i></i></div>
  <div class="fbrand"><i></i>BRAMBLEWOOD</div>
  <div style="line-height:17.6px">copyright©2015.Bramblewood Joinery<br>All Rights Reserved</div>
</div>
<div class="abs fseal">Bramblewood<br>Joinery</div>
</body>
</html>
```